Keystonery Billboard - Financial Services Company (Investments, Tax Planning and Insurance)

Our new office has a billboard directly above the office building. We'd like something eye-catching with a strong Call to Action, with the main part of the billboard being under 7 words if possible. We'd like you to include a way to get ahold of us (either our website keystoneryllc.example or our phone number 302-418-2907. You may also include in small font something to indicate that we've been serving the area since 1980 (the DE area, the tri-state area, the Marlowe Hollow, etc.)

We offer financial planning, tax planning, and insurance, and we help our clients to focus on their goals and happiness by providing everything they need for lifelong wealth under one roof.

Our logos are attached, we use a triangle logo with green and gray. We use the tagline "discover lasting prosperity" but this does not need to be included.

Potential ideas we have seen from other financial companies-
- the concept that the driver spends more time looking at billboards than planning for their retirement
-something along the lines of "everything you need for your finances is in this building right here" planning, investments, taxes, insurance"
-don't spend your time worrying about retirement, let us help you plan for it
-are you working for your money, or is it working for you?
- retirement takes planning, we're here to help
- ready to retire? talk to us
- need investment advice?
- need help investing?
- crossing your fingers isn't a retirement plan. we can help.
- retiring soon? you need help.

Those are just general ideas, please feel free to be creative.

brand colors:
#00b585
#00b185
#000000
#ffffff
#6d6f75
#6d6f75
#6f7074
#021712
#052e24

```html
<!DOCTYPE html>
<html lang="en">
<head>
<meta charset="utf-8">
<title>Keystonery Billboard</title>
<link rel="stylesheet" href="https://fonts.googleapis.com/css2?family=Poppins:wght@500;600;700;800&family=Oswald:wght@600&display=swap">
<style>
  :root {
    --green: #00b585;
    --green-deep: #009a70;
    --ink: #3f3f44;
    --gray: #6d6f75;
    --light-gray: #d4d5d7;
    --dark-green: #052e24;
    --text: #2b2b2b;
    --white: #ffffff;
    --backdrop: #eef0f1;
  }
  * { margin: 0; padding: 0; box-sizing: border-box; }
  html, body { width: 1117px; height: 1200px; overflow: hidden; }
  body {
    background: var(--backdrop);
    font-family: "Poppins", sans-serif;
    position: relative;
  }
  .billboard {
    position: absolute;
    left: 38px; top: 447px;
    width: 1040px; height: 304px;
    background: var(--white);
    box-shadow: 0 14px 30px rgba(0,0,0,.18);
    overflow: hidden;
  }
  .backdrop-shapes { position: absolute; inset: 0; }
  .headline {
    position: absolute; left: 24px; top: 14px;
    font-size: 81px; font-weight: 800; line-height: 1;
    letter-spacing: -2px; color: var(--ink); white-space: nowrap;
  }
  .cta {
    position: absolute; left: 29px; top: 102px; height: 66px;
    display: flex; align-items: center;
    color: var(--white); font-weight: 700; white-space: nowrap;
  }
  .cta-label { font-size: 45px; letter-spacing: -1px; }
  .cta-icon { width: 42px; height: 42px; flex: none; margin: 0 10px 0 12px; }
  .cta-phone { font-size: 50px; letter-spacing: -0.5px; }
  .services { list-style: none; font-size: 13px; font-weight: 500; color: var(--text); }
  .services li {
    position: absolute; top: 183px;
    display: flex; align-items: center; gap: 6px; white-space: nowrap;
  }
  .services .svc-financial { left: 20px; }
  .services .svc-investment { left: 183px; }
  .services .svc-tax { left: 394px; }
  .services .svc-insurance { left: 517px; }
  .tick { width: 14px; height: 14px; flex: none; }
  .brand { position: absolute; left: 23px; top: 222px; }
  .brand-name {
    display: flex; align-items: center; gap: 10px;
    font-size: 34px; font-weight: 600; line-height: 1;
    color: var(--green-deep); letter-spacing: -0.5px; white-space: nowrap;
  }
  .brand-mark { width: 28px; height: 28px; background: var(--green); }
  .brand-tagline {
    margin: 6px 0 0 40px;
    font-size: 7.5px; font-weight: 500; letter-spacing: 3px;
    text-transform: uppercase; color: var(--gray); white-space: nowrap;
  }
  .url {
    position: absolute; left: 312px; top: 235px;
    font-size: 17px; font-weight: 700; color: var(--dark-green); white-space: nowrap;
  }
  .seal {
    position: absolute; left: 610px; top: 168px;
    width: 114px; height: 114px;
  }
  .seal svg { position: absolute; inset: 0; }
  .seal-text {
    position: absolute; inset: 0;
    display: flex; flex-direction: column; align-items: center; justify-content: center;
    text-align: center; color: var(--white);
    font-size: 13px; font-weight: 600; line-height: 1.15; padding-top: 4px;
  }
  .seal-year {
    font-family: "Oswald", sans-serif; font-size: 34px;
    color: var(--dark-green); line-height: 1.05;
  }
</style>
</head>
<body>
  <main class="billboard">
    <svg class="backdrop-shapes" width="1040" height="304" viewBox="0 0 1040 304">
      <defs>
        <linearGradient id="photoTone" x1="0" y1="0" x2="1" y2="1">
          <stop offset="0" stop-color="#d8d3cb"/>
          <stop offset="0.55" stop-color="#e9cdd3"/>
          <stop offset="1" stop-color="#c7c9cd"/>
        </linearGradient>
      </defs>
      <polygon points="593,304 810,0 920,0 1040,210 1040,304" fill="var(--light-gray)"/>
      <rect x="0" y="102" width="309" height="66" fill="var(--green)"/>
      <polygon points="309,102 772,102 689,168 309,168" fill="var(--gray)"/>
      <polygon class="photo" role="img" aria-label="Photo of a smiling retired couple sharing a laptop on a sofa"
        points="657,304 800,60 1040,60 1040,304" fill="url(#photoTone)"/>
    </svg>

    <h1 class="headline">READY TO RETIRE?</h1>

    <div class="cta">
      <span class="cta-label">TALK TO US</span>
      <svg class="cta-icon" viewBox="0 0 42 42" aria-hidden="true">
        <circle cx="21" cy="21" r="21" fill="var(--white)"/>
        <path d="M14 11c1.2-.8 2.3-.6 3 .6l2.2 3.6c.6 1 .3 2.1-.6 2.7l-1.5 1c.9 2.3 2.7 4.3 5 5.4l1.1-1.5c.7-.9 1.8-1.1 2.7-.5l3.6 2.3c1.1.7 1.3 1.9.5 3-1.4 2-3.6 2.9-5.9 2.2-5.6-1.8-10-6.2-11.700-11.8-.7-2.3.3-4.5 1.6-5.9z" fill="var(--green)"/>
      </svg>
      <span class="cta-phone">302-418-2907</span>
    </div>

    <ul class="services">
      <li class="svc-financial"><svg class="tick" viewBox="0 0 14 14" aria-hidden="true"><rect x="1" y="2" width="11" height="11" fill="none" stroke="var(--green-deep)" stroke-width="1.6"/><path d="M3.5 7.5l2.5 2.5 6-8" fill="none" stroke="var(--green-deep)" stroke-width="2"/></svg>Financial Planning</li>
      <li class="svc-investment"><svg class="tick" viewBox="0 0 14 14" aria-hidden="true"><rect x="1" y="2" width="11" height="11" fill="none" stroke="var(--green-deep)" stroke-width="1.6"/><path d="M3.5 7.5l2.5 2.5 6-8" fill="none" stroke="var(--green-deep)" stroke-width="2"/></svg>Investment Management</li>
      <li class="svc-tax"><svg class="tick" viewBox="0 0 14 14" aria-hidden="true"><rect x="1" y="2" width="11" height="11" fill="none" stroke="var(--green-deep)" stroke-width="1.6"/><path d="M3.5 7.5l2.5 2.5 6-8" fill="none" stroke="var(--green-deep)" stroke-width="2"/></svg>Tax Planning</li>
      <li class="svc-insurance"><svg class="tick" viewBox="0 0 14 14" aria-hidden="true"><rect x="1" y="2" width="11" height="11" fill="none" stroke="var(--green-deep)" stroke-width="1.6"/><path d="M3.5 7.5l2.5 2.5 6-8" fill="none" stroke="var(--green-deep)" stroke-width="2"/></svg>Insurance</li>
    </ul>

    <div class="brand">
      <div class="brand-name"><span class="brand-mark"></span>Keystonery</div>
      <p class="brand-tagline">discover lasting prosperity</p>
    </div>

    <p class="url">www.KEYSTONERYLLC.example</p>

    <div class="seal">
      <svg viewBox="0 0 114 114" aria-hidden="true">
        <defs>
          <radialGradient id="sealTone" cx="0.5" cy="0.45" r="0.6">
            <stop offset="0" stop-color="#2fd3a2"/>
            <stop offset="1" stop-color="#009a70"/>
          </radialGradient>
        </defs>
        <circle cx="57" cy="57" r="56" fill="var(--green-deep)"/>
        <circle cx="57" cy="57" r="56" fill="none" stroke="var(--white)" stroke-width="3" stroke-dasharray="3 4"/>
        <circle cx="57" cy="57" r="50" fill="url(#sealTone)"/>
      </svg>
      <div class="seal-text">
        <span>SERVING</span>
        <span>THE AREA</span>
        <span>SINCE</span>
        <span class="seal-year">1980</span>
      </div>
    </div>
  </main>
</body>
</html>
```